BildeVOLD buisnesscard

Hey :) I need a modern buisnesscard for my company BildeVOLD
It most have:
Dagligleder og Fotograf: Henrik Audun Strandvik

Mob: +4791264085
Epost: post@bildevold.example
Adresse: Kvernbakken9, 6040 Langevåg

Facbook and instagram logo with text BildeVOLD

BildeVOLD logo

It Company

```html
<!DOCTYPE html>
<html lang="no">
<head>
<meta charset="utf-8">
<title>BildeVOLD – visittkort</title>
<link rel="stylesheet" href="https://fonts.googleapis.com/css2?family=Noto+Sans:wght@400;600&display=swap">
<style>
  :root {
    --backdrop: #e4e4e4;
    --card: #232323;
    --ink: #a6a6a6;
    --band: #a3a3a3;
    --band-ink: #1e1e1e;
  }
  * { margin: 0; padding: 0; box-sizing: border-box; }
  html, body { width: 1200px; height: 1200px; overflow: hidden; }
  body {
    background: var(--backdrop);
    font-family: "Noto Sans", Verdana, sans-serif;
    color: var(--ink);
    position: relative;
  }
  .card {
    position: absolute;
    width: 722px;
    height: 434px;
    background: var(--card);
    overflow: hidden;
  }
  .card--front { left: 240px; top: 106px; }
  .card--back { left: 238px; top: 624px; }

  .brand-name {
    position: absolute;
    font-weight: 600;
    color: var(--ink);
    white-space: nowrap;
  }
  .card--front .brand-name {
    left: 0; width: 330px; text-align: center;
    top: 222px; font-size: 40px; letter-spacing: 0.5px;
  }
  .card--back .brand-name {
    left: 0; width: 722px; text-align: center;
    top: 176px; font-size: 58px;
  }

  .person-name {
    position: absolute; left: 350px; top: 98px;
    font-size: 26px; font-weight: 400; letter-spacing: 0.6px;
  }
  .person-role {
    position: absolute; left: 351px; top: 134px;
    font-size: 16px; letter-spacing: 0.8px;
  }
  .contact-list { list-style: none; }
  .contact-item {
    position: absolute; left: 351px;
    display: flex; align-items: flex-start; gap: 16px;
    font-size: 19px; letter-spacing: 0.8px; line-height: 24px;
  }
  .contact-item svg { flex: none; width: 30px; height: 30px; }
  .contact-item--address { top: 174px; }
  .contact-item--address .contact-text { margin-top: 4px; }
  .contact-item--phone { top: 235px; }
  .contact-item--phone .contact-text { margin-top: 3px; margin-left: 2px; }
  .contact-item--email { top: 278px; }
  .contact-item--email .contact-text { margin-top: 2px; }

  .web-band { position: absolute; left: 0; top: 378px; width: 722px; height: 36px; }
  .web-address {
    position: absolute; left: 122px; top: 382px;
    font-size: 17px; letter-spacing: 3px; color: var(--band-ink);
  }

  .social-row {
    position: absolute; left: 0; top: 338px; width: 722px;
    display: flex; justify-content: center; gap: 26px;
    font-size: 19px; letter-spacing: 0.6px;
  }
  .social-link { display: flex; align-items: center; gap: 12px; }
  .social-mark {
    width: 32px; height: 32px; border-radius: 50%;
    border: 2px solid var(--ink);
  }
</style>
</head>
<body>

<section class="card card--front" aria-label="Forside">
  <div class="brand-name">BildeVOLD</div>

  <h1 class="person-name">Henrik Audun Strandvik</h1>
  <p class="person-role">Dagligleder og Fotograf</p>

  <ul class="contact-list">
    <li class="contact-item contact-item--address">
      <svg viewBox="0 0 30 30" aria-hidden="true">
        <circle cx="15" cy="15" r="15" fill="var(--ink)"/>
        <path d="M15 6.5a6 6 0 0 0-6 6c0 4.5 6 11 6 11s6-6.5 6-11a6 6 0 0 0-6-6z" fill="var(--card)"/>
        <circle cx="15" cy="12.5" r="2.2" fill="var(--ink)"/>
      </svg>
      <span class="contact-text">Kvernbakken9<br>6040 Langevåg</span>
    </li>
    <li class="contact-item contact-item--phone">
      <svg viewBox="0 0 30 30" aria-hidden="true">
        <circle cx="15" cy="15" r="15" fill="var(--ink)"/>
        <path d="M10.5 7.5l3 3.2-1.6 2.1c.9 2 2.4 3.5 4.3 4.4l2.1-1.6 3.2 3-1.4 2.6c-5.5-.3-10.9-5.7-11.2-11.2z" fill="var(--card)"/>
      </svg>
      <span class="contact-text">479 126 4085</span>
    </li>
    <li class="contact-item contact-item--email">
      <svg viewBox="0 0 30 30" aria-hidden="true">
        <circle cx="15" cy="15" r="15" fill="var(--ink)"/>
        <rect x="8" y="10" width="14" height="10" rx="1" fill="var(--card)"/>
        <path d="M8.5 10.8L15 15.8l6.5-5" fill="none" stroke="var(--ink)" stroke-width="1.3"/>
      </svg>
      <span class="contact-text">post@bildevold.example</span>
    </li>
  </ul>

  <svg class="web-band" viewBox="0 0 722 36" aria-hidden="true">
    <polygon points="0,0 516,0 530,36 0,36" fill="var(--band)"/>
    <polygon points="524,0 722,0 722,36 538,36" fill="var(--band)"/>
  </svg>
  <span class="web-address">www.bildevold</span>
</section>

<section class="card card--back" aria-label="Bakside">
  <div class="brand-name">BildeVOLD</div>
  <div class="social-row">
    <span class="social-link"><span class="social-mark"></span>BildeVOLD</span>
    <span class="social-link"><span class="social-mark"></span>BildeVOLD</span>
  </div>
</section>

</body>
</html>
```